I work in creative/artistic projects across different mediums.
It needs to communicate creativity, style, sexy, uniqueness, individuality and sophistication.
It should not look corporate.
Colours I like are black silver gold deep purple, chocolate, orchid.
It doesn't have to make use of all these colours.
I do not like bright primary colors.
Updates

Project Deadline Extended
Reason: Still in the communication process and to allow the person enough time to finish the design. Though i should know in the next day or two. Thank you.

Target Market(s)

creatives and companies wanting to inject creativity into thier business.

Industry/Entity Type

Work

Contact Information for Business Card

Corwin Haldley
0418592036
corwin@corwinhaldley-example.com

quietgoldenhourstudio.example.au

Requirements
Should not have
• Anything corporate OR OLD FASHIONED

```html
<!DOCTYPE html>
<html lang="en">
<head>
<meta charset="utf-8">
<title>Corwin Haldley — Business Card</title>
<link rel="stylesheet" href="https://fonts.googleapis.com/css2?family=Mulish:wght@700;800&display=swap">
<style>
  :root {
    --page-bg: #f5f7f8;
    --card-charcoal: #48474a;
    --band-gold: #d7b77a;
    --band-caramel: #bb9b66;
    --band-chocolate: #947753;
    --rim-grey: #6e6d70;
    --seam-dark: #3a3836;
    --name-tan: #bc9969;
    --contact-white: #ffffff;
    --swirl-gold: #c9a86c;
    --swirl-silver: #8c8b8f;
  }
  html, body {
    margin: 0;
    padding: 0;
    width: 1200px;
    height: 761px;
    overflow: hidden;
    background: var(--page-bg);
  }
  .stage {
    position: relative;
    width: 1200px;
    height: 761px;
  }
  .business-card {
    position: absolute;
    left: 315px;
    top: 223px;
    width: 556px;
    height: 334px;
    display: block;
  }
  .contact-line {
    font-family: "Mulish", "Century Gothic", sans-serif;
    font-weight: 700;
    fill: var(--contact-white);
  }
  .contact-phone { font-size: 16px; letter-spacing: 0.5px; }
  .contact-email { font-size: 14px; letter-spacing: 0.2px; }
  .contact-web { font-size: 15px; letter-spacing: 0.2px; }
  .card-name {
    font-family: "Mulish", "Century Gothic", sans-serif;
    font-weight: 800;
    font-size: 33px;
    letter-spacing: 1px;
    fill: var(--name-tan);
  }
</style>
</head>
<body>
<main class="stage">
  <svg class="business-card" viewBox="0 0 556 334" xmlns="http://www.w3.org/2000/svg" aria-label="Business card for Corwin Haldley">
    <defs>
      <clipPath id="card-clip"><rect width="556" height="334"/></clipPath>
      <radialGradient id="gold-swirl-tone" cx="0.5" cy="0.5" r="0.5">
        <stop offset="0" stop-color="var(--swirl-gold)" stop-opacity="0.55"/>
        <stop offset="1" stop-color="var(--swirl-gold)" stop-opacity="0"/>
      </radialGradient>
      <radialGradient id="silver-swirl-tone" cx="0.5" cy="0.5" r="0.5">
        <stop offset="0" stop-color="var(--swirl-silver)" stop-opacity="0.35"/>
        <stop offset="1" stop-color="var(--swirl-silver)" stop-opacity="0"/>
      </radialGradient>
      <path id="arc-phone" d="M98.1 144.5 A216 216 0 0 0 216 -48"/>
      <path id="arc-email" d="M84.1 210.7 A272 272 0 0 0 270.9 -71.7"/>
      <path id="arc-web" d="M98.8 275.2 A338 338 0 0 0 338 -48"/>
    </defs>

    <g clip-path="url(#card-clip)">
      <rect class="card-ground" width="556" height="334" fill="var(--card-charcoal)"/>

      <g class="flourish-area">
        <ellipse role="img" aria-label="Silver flowing swirl ornament, upper right" cx="450" cy="90" rx="120" ry="80" fill="url(#silver-swirl-tone)"/>
        <ellipse role="img" aria-label="Silver flowing swirl ornament, lower right" cx="420" cy="270" rx="150" ry="70" fill="url(#silver-swirl-tone)"/>
      </g>

      <g class="arc-bands">
        <circle class="band-rim" cx="0" cy="-48" r="377" fill="var(--rim-grey)"/>
        <circle class="band-chocolate" cx="0" cy="-48" r="370" fill="var(--band-chocolate)"/>
        <circle class="band-seam" cx="0" cy="-48" r="299" fill="var(--seam-dark)" opacity="0.6"/>
        <circle class="band-caramel" cx="0" cy="-48" r="297" fill="var(--band-caramel)"/>
        <circle class="band-seam" cx="0" cy="-48" r="238" fill="var(--seam-dark)" opacity="0.6"/>
        <circle class="band-gold" cx="0" cy="-48" r="236" fill="var(--band-gold)"/>
      </g>

      <ellipse role="img" aria-label="Gold spiral swirl ornament" cx="75" cy="50" rx="95" ry="70" fill="url(#gold-swirl-tone)"/>

      <g class="contact-icons" fill="var(--contact-white)">
        <path class="icon-phone" d="M50 139 c3 -3 6 -3 8 0 l4 5 c1 2 1 4 -1 5 l-2 2 c2 5 6 9 11 11 l2 -2 c1 -2 3 -2 5 -1 l5 4 c3 2 3 5 0 8 l-3 3 c-10 4 -30 -16 -32 -28 z"/>
        <g class="icon-mail">
          <rect x="45" y="203" width="33" height="24" fill="var(--contact-white)"/>
          <path d="M45 203 L61.5 218 L78 203 M45 227 L57 215 M78 227 L66 215" fill="none" stroke="var(--band-caramel)" stroke-width="1.6"/>
        </g>
        <g class="icon-globe">
          <circle cx="63" cy="284" r="17"/>
          <g fill="none" stroke="var(--band-chocolate)" stroke-width="1.4">
            <ellipse cx="63" cy="284" rx="7" ry="17"/>
            <line x1="46" y1="278" x2="80" y2="278"/>
            <line x1="46" y1="290" x2="80" y2="290"/>
          </g>
          <rect x="46" y="280" width="34" height="8" fill="var(--contact-white)"/>
          <text x="63" y="287.5" text-anchor="middle" font-family="Mulish, sans-serif" font-weight="800" font-size="8" fill="var(--band-chocolate)">www</text>
        </g>
      </g>

      <text class="contact-line contact-phone"><textPath href="#arc-phone" startOffset="8">0418 592 036</textPath></text>
      <text class="contact-line contact-email"><textPath href="#arc-email" startOffset="4">corwin@corwinhaldley-example.com</textPath></text>
      <text class="contact-line contact-web"><textPath href="#arc-web" startOffset="6">www.quietgoldenhourstudio.example.au</textPath></text>

      <text class="card-name" x="513" y="292" text-anchor="end">Corwin Haldley</text>
    </g>
  </svg>
</main>
</body>
</html>
```